A paperback book cover entitled: The Keystone

1. For the front cover of the paperback I need the photo of me walking down the driveway at Wexcombe Hall as the focal point. The designer will use their discretion where to insert the book title: The Keystone.
Also the designer will use their discretion where my name Desmond Harrowby as the author is placed. Attached is a contemporary photo of me to use if the designer thinks that possible. Both these photos are attached.
2. The back cover page will contain two main written insertions (1) About the Book and (2) About the Author.
The book will be an 8.5x11 inch paperback of some 570 pages published by Brindlepress.
About the book:
This book is about Australian Public Affairs 1957-2020 as perceived and observed by Desmond Harrowby. It has a significant but not exclusive Queensland focus concerning History, Commentary, and Anecdotes, plus some things Desmond has been involved with along the way.
Desmond developed unique Transition to Government and Transition to Opposition plans that have all been implemented. Some of those plans are referred to in the book and other Transition plans are appendixes to the book.
Now at 73 years of age, Desmond’s motivation for writing this book is to ensure a wealth of historical scenarios are captured and incorporated into the public record for future generations.

About the author:

Desmond Harrowby has been a largely silent and invisible political confidant to Australian Premiers and Prime Ministers.
Desmond worked in the Queensland public sector from 1971-2009 as Chief of Staff to four Queensland State Opposition Leaders for 13 years and then as a Public Sector senior executive.
He subsequently served on the Edith Tarrant Foundation Board, the Orrin Vale Records Hall Board, and consulted to a mining company. He has recorded many Oral History projects for The Fernwick Archive in Canberra.
Over the last 30+ years, he has been approached countless times for advice relating to Business, Government, Authors, Historians, and people seeking a job. He has never charged a cent for any of his advice, even when not working within Government.
There are two extra photos attached to maybe be on each side at the bottom of the back cover if the designer thinks it is appropriate.
Those in the 4 person photo from the left were all connected with the Tallowmere Assembly: former Unity Minister Neil Corrigan, Former Heartland Party Premier Tom Beaulieu, former Progress Leader Glen Osborne, and Desmond Harrowby

In the three person photo from the left are: Desmond Harrowby, Former PM Rupert Danforth, and Prime Minister Brian Ferrow.

3. In the spine of the book will be simply (1) The Keystone and (2) Desmond Harrowby

Here’s hoping a good design is created.

```html
<!DOCTYPE html>
<html lang="en">
<head>
<meta charset="utf-8">
<title>The Keystone – Cover</title>
<link href="https://fonts.googleapis.com/css2?family=Anton&family=Cabin:wght@400;500&display=swap" rel="stylesheet">
<style>
  :root {
    --cover-red: #8a1c0c;
    --sepia-dark: #5a2a1e;
    --sepia-mid: #9a6453;
    --sepia-light: #d9b5a6;
    --ink: #111;
    --paper: #fff;
  }
  * { margin: 0; padding: 0; box-sizing: border-box; }
  html, body { width: 1200px; height: 838px; overflow: hidden; background: var(--cover-red); }
  .cover { position: relative; width: 1200px; height: 838px; background: var(--cover-red); font-family: "Cabin", sans-serif; color: var(--paper); }
  .display { font-family: "Anton", sans-serif; }
  .back-title, .spine-art, .front-title { position: absolute; }
  .back-title { left: 50px; top: 30px; }
  .spine-art { left: 545px; top: 55px; }
  .about-book { position: absolute; left: 54px; top: 216px; width: 460px; font-size: 10px; line-height: 13.5px; }
  .about-book p { margin-bottom: 13px; }
  .about-book p.tight { margin-bottom: 0; }
  .photo { position: absolute; }
  .photo-group-four { left: 101px; top: 363px; width: 131px; height: 99px; background: linear-gradient(160deg, #d8d4cc, #8a8276 60%, #4b4740); }
  .photo-group-three { left: 314px; top: 363px; width: 140px; height: 99px; background: linear-gradient(160deg, #d9c49a, #7d6447 55%, #2f2620); }
  .caption { position: absolute; top: 469px; font-size: 7px; line-height: 9.5px; text-align: center; }
  .caption-four { left: 46px; width: 240px; }
  .caption-three { left: 284px; width: 200px; }
  .about-author-heading { position: absolute; left: 0; width: 512px; top: 516px; text-align: center; font-size: 10px; font-weight: 500; letter-spacing: 0.2px; }
  .author-lede { position: absolute; left: 52px; top: 539px; font-size: 8.5px; }
  .photo-author { left: 54px; top: 556px; width: 74px; height: 94px; border: 1px solid #ddd; background: linear-gradient(180deg, #c9ccd1, #6c7179 55%, #1e2430); }
  .author-bio { position: absolute; left: 133px; top: 555px; width: 370px; font-size: 8.2px; line-height: 10.8px; }
  .author-bio p { margin-bottom: 10.8px; }
  .front-photo { left: 662px; top: 0; width: 538px; height: 838px;
    background:
      radial-gradient(ellipse at 60% 25%, rgba(240,210,195,.55), transparent 45%),
      radial-gradient(ellipse at 65% 70%, rgba(200,150,135,.45), transparent 50%),
      linear-gradient(90deg, var(--sepia-dark), var(--sepia-mid) 35%, var(--sepia-light) 60%, var(--sepia-mid) 85%, var(--sepia-dark)); }
  .front-title { left: 662px; top: 0; }
</style>
</head>
<body>
<main class="cover">

  <!-- Back cover -->
  <svg class="back-title display" width="460" height="175" viewBox="0 0 460 175" aria-label="The Keystone">
    <text x="192" y="30" font-family="Anton, sans-serif" font-size="32" fill="#fff" textLength="36" lengthAdjust="spacingAndGlyphs">THE</text>
    <text x="3" y="169" font-family="Anton, sans-serif" font-size="168" fill="#fff" stroke="#111" stroke-width="2.5" paint-order="stroke" textLength="446" lengthAdjust="spacingAndGlyphs">KEYSTONE</text>
  </svg>

  <section class="about-book">
    <p>This book is about Australian Public Affairs 1957-2020 as perceived and observed by Desmond Harrowby.</p>
    <p class="tight">It has a significant but not exclusive Queensland focus concerning History, Commentary, and Anecdotes, plus some things Desmond has been involved with along the way.</p>
    <p class="tight">Desmond developed unique Transition to Government and Transition to Opposition plans that have all been implemented.</p>
    <p>Some of those plans are referred to in the book and other Transition plans are appendixes to the book.</p>
    <p>Now at 73 years of age, Desmond’s motivation for writing this book is to ensure a wealth of historical scenarios are captured and incorporated into the public record for future generations.</p>
  </section>

  <div class="photo photo-group-four" role="img" aria-label="Photo of four men standing together in a room"></div>
  <div class="photo photo-group-three" role="img" aria-label="Photo of three men, one seated, in a study"></div>
  <p class="caption caption-four">Unity Minister Neil Corrigan, Heartland Party Premier Tom Beaulieu,<br>Progress Leader Glen Osborne, and Desmond Harrowby</p>
  <p class="caption caption-three">Desmond Harrowby,<br>Former PM Rupert Danforth, and Prime Minister Brian Ferrow.</p>

  <h2 class="about-author-heading">ABOUT THE AUTHOR</h2>
  <p class="author-lede">Desmond Harrowby has been a largely silent and invisible political confidant to Australian Premiers and Prime Ministers.</p>
  <div class="photo photo-author" role="img" aria-label="Portrait of the author in a dark suit"></div>
  <section class="author-bio">
    <p>Desmond worked in the Queensland public sector from 1971-2009 as Chief of Staff to four Queensland State Opposition Leaders for 13 years and then as a Public Sector senior executive. He subsequently served on the Edith Tarrant Foundation Board, the Orrin Vale Records Hall Board, and consulted to a mining company. He has recorded many Oral History projects for The Fernwick Archive in Canberra.</p>
    <p>Over the last 30+ years, he has been approached countless times for advice relating to Business, Government, Authors, Historians, and people seeking a job.<br>He has never charged a cent for any of his advice, even when not working within Government.</p>
  </section>

  <!-- Spine -->
  <svg class="spine-art" width="110" height="680" viewBox="0 0 110 680" aria-label="Spine: Desmond Harrowby, The Keystone">
    <g transform="translate(7,10) rotate(90)">
      <text x="0" y="0" font-family="Anton, sans-serif" font-size="36" fill="#fff" stroke="#111" stroke-width="1.5" paint-order="stroke" textLength="300" lengthAdjust="spacingAndGlyphs">DESMOND HARROWBY</text>
    </g>
    <g transform="translate(83,309) rotate(90)">
      <text x="0" y="0" font-family="Anton, sans-serif" font-size="24" fill="#fff" textLength="28" lengthAdjust="spacingAndGlyphs">THE</text>
    </g>
    <g transform="translate(5,341) rotate(90)">
      <text x="0" y="0" font-family="Anton, sans-serif" font-size="118" fill="#fff" stroke="#111" stroke-width="2.5" paint-order="stroke" textLength="333" lengthAdjust="spacingAndGlyphs">KEYSTONE</text>
    </g>
  </svg>

  <!-- Front cover -->
  <div class="photo front-photo" role="img" aria-label="Sepia photo of the author as a young man walking down the driveway at Wexcombe Hall"></div>
  <svg class="front-title" width="538" height="838" viewBox="0 0 538 838" aria-label="The Keystone by Desmond Harrowby">
    <text x="24" y="188" font-family="Anton, sans-serif" font-size="58" fill="#fff" textLength="78" lengthAdjust="spacingAndGlyphs">THE</text>
    <text x="28" y="340" font-family="Anton, sans-serif" font-size="180" fill="rgba(255,255,255,0.22)" stroke="#fff" stroke-width="2.5" textLength="472" lengthAdjust="spacingAndGlyphs">KEYSTONE</text>
    <text x="56" y="740" font-family="Anton, sans-serif" font-size="58" fill="#fff" textLength="412" lengthAdjust="spacingAndGlyphs">DESMOND HARROWBY</text>
  </svg>

</main>
</body>
</html>
```